Social Media Graphics - Oakline Push REVISED

Create 6-7 individual social media graphics (square size) to encourage folks to join our online course called:

The Harvest Ledger Circle
How to Launch a Multi-Million Business From Scratch
Sign Up Today!

IMPORTANT: Make the largest and most prominent text on the graphic be: How to Launch a Multi-Million Business From Scratch

For the color scheme of the graphics, let's try a blue color palette; make sure the graphics appeal to both men and women

Make sure each graphic contains 1 of the 3 pics attached (crop pic as needed); and make sure one of the graphics is all TEXT only.

Target Market(s)

men and women looking to start a business

Industry/Entity Type

Entrepreneurship

Colors
0054AA
0677BA
7BADD7
CADEEF
E8F1F8

Requirements
Must have
• All the text and use the 3 pics provided; one graphic can be all text; Simple, modern design that's easy to read

```html
<!DOCTYPE html>
<html lang="en">
<head>
<meta charset="utf-8">
<title>Oakline Push – Social Graphic</title>
<link rel="stylesheet" href="https://fonts.googleapis.com/css2?family=Poppins:wght@600;700;800;900&family=Anton&family=Great+Vibes&display=swap">
<style>
  :root{
    --page:#d4d4d4;
    --navy:#0b1a3a;
    --navy-deep:#081430;
    --magenta:#c2378f;
    --pink:#f0356a;
    --white:#ffffff;
    --blue-bright:#1fa2f0;
    --blue-mid:#0677ba;
    --blue-brand:#0054aa;
    --blue-soft:#7badd7;
    --gold:#ffb000;
    --gold-deep:#b47a12;
  }
  *{margin:0;padding:0;box-sizing:border-box}
  html,body{width:1200px;height:930px;overflow:hidden;background:var(--page)}
  .graphic{
    position:absolute;left:150px;top:15px;width:900px;height:900px;overflow:hidden;
    background:
      radial-gradient(ellipse 420px 380px at 660px 560px, rgba(194,55,143,.55), transparent 70%),
      radial-gradient(ellipse 300px 260px at 280px 520px, rgba(6,119,186,.45), transparent 70%),
      linear-gradient(180deg,var(--navy-deep) 0%,var(--navy) 60%,#1b1d4a 100%);
    font-family:'Poppins',sans-serif;
  }
  .skyline{position:absolute;left:520px;top:0;width:380px;height:420px;
    background:linear-gradient(180deg,rgba(11,26,58,0) 0%,rgba(20,60,110,.55) 60%,rgba(11,26,58,0) 100%)}
  .kicker{position:absolute;left:64px;top:80px;color:var(--pink);font-weight:700;font-size:34px;letter-spacing:.09em;line-height:1}
  .headline{position:absolute;left:60px;top:124px;font-weight:900;font-size:112px;line-height:86px;letter-spacing:-.035em;text-transform:uppercase}
  .headline span{display:block}
  .headline .line-white{color:var(--white)}
  .headline .line-blue{background:linear-gradient(180deg,var(--blue-bright),#2d8ff0 60%,#1a6fe0);-webkit-background-clip:text;background-clip:text;color:transparent}
  .dollar-art{position:absolute;left:557px;top:299px;width:76px;height:109px;border-radius:10px;
    background:linear-gradient(160deg,#ffe08a,var(--gold) 45%,var(--gold-deep))}
  .from{position:absolute;left:62px;top:430px;font-family:'Great Vibes',cursive;color:var(--pink);font-size:66px;line-height:1}
  .scratch{position:absolute;left:64px;top:500px;font-family:'Anton',sans-serif;color:var(--gold);font-size:64px;line-height:1;letter-spacing:.01em}
  .chart{position:absolute;left:0;top:570px;width:360px;height:150px}
  .cta{position:absolute;left:65px;top:771px;width:280px;height:58px;border-radius:29px 0 0 29px;
    background:linear-gradient(180deg,#6fc0ff,#2f86ea 55%,#1d6ad6);color:var(--white);font-weight:800;font-size:23px;
    display:flex;align-items:center;padding-left:28px;letter-spacing:.005em}
  .hosts-photo{position:absolute;left:329px;top:430px;width:502px;height:470px;
    border-radius:200px 200px 0 0;
    background:linear-gradient(180deg,rgba(120,50,110,.85),#3a1d3e 45%,#c8264f 75%,#1d1424)}
  .brand-name{position:absolute;font-weight:700;color:var(--blue-brand);opacity:.9;
    font-size:140px;line-height:1;white-space:nowrap;transform-origin:0 0;transform:rotate(90deg);
    left:852px;top:84px;letter-spacing:-.01em}
  .brand-tag{position:absolute;font-weight:600;color:var(--white);font-size:23px;letter-spacing:.42em;white-space:nowrap;
    transform-origin:0 0;transform:rotate(90deg);left:700px;top:88px}
</style>
</head>
<body>
<main class="graphic">
  <div class="skyline" role="img" aria-label="Night city skyline with floating currency symbols"></div>

  <p class="kicker">HOW TO LAUNCH A</p>
  <h1 class="headline">
    <span class="line-white">Multi</span>
    <span class="line-white">Million</span>
    <span class="line-blue">Busines</span>
  </h1>
  <div class="dollar-art" role="img" aria-label="Shiny gold dollar sign"></div>

  <p class="from">From</p>
  <p class="scratch">SCRATCH</p>

  <svg class="chart" viewBox="0 0 360 150" aria-hidden="true">
    <line x1="0" y1="122" x2="360" y2="122" stroke="#3aa0ff" stroke-width="2" opacity=".7"/>
    <g fill="#4aa8ff" opacity=".8">
      <polygon points="130,122 140,95 150,122"/>
      <polygon points="160,122 172,80 184,122"/>
      <polygon points="200,122 214,65 228,122"/>
      <polygon points="250,122 264,50 278,122"/>
      <polygon points="300,122 316,30 332,122"/>
    </g>
    <g fill="#7badd7">
      <polygon points="132,40 140,24 148,40"/>
      <polygon points="306,18 316,2 326,18"/>
    </g>
    <rect x="137" y="40" width="6" height="82" fill="#7badd7" opacity=".5"/>
    <polyline points="90,122 140,110 185,100 230,70 270,95 310,80 350,88" fill="none" stroke="#ff6a7a" stroke-width="2"/>
    <polyline points="90,125 150,118 200,110 250,85 300,70 350,60" fill="none" stroke="#9fd4ff" stroke-width="2"/>
    <circle cx="230" cy="70" r="4" fill="#ffd0d0"/>
    <circle cx="150" cy="118" r="3" fill="#ffffff"/>
  </svg>

  <div class="cta">SIGN UP TODAY!</div>

  <div class="hosts-photo" role="img" aria-label="Smiling woman in a pink dress with arms crossed beside a smiling man in a black tee and jacket, upward arrow glow behind them"></div>

  <p class="brand-tag">LEDGER CIRCLE</p>
  <p class="brand-name">HARVEST</p>
</main>
</body>
</html>
```